Ward Compass Business Card Design*

We need a business card design for our company Ward Compass. Our company is specialized in providing online consulting services regarding medical institutions, hospitals and doctors. We work with patients worldwide looking to choose between healthcare providers. We have a website you may use as a reference, where we list doctors and clinics worldwide. So we target Medical providers as well as patients worldwide.
Target Market(s)
Medical Providers and patients around the world
Industry/Entity Type
Medical
Contact Information for Business Card
Salwa Kettani
CEO
+90 612 348 2175
info@wardcompass.example
www.wardcompass.example
14 Annakhil 7 H.R.B. Rabat, Morocco
Requirements
Must have
- Company logo/name on one full side, personal info and smaller logo and company name on the other side.
Nice to have
- Smart and elegant design

```html
<!DOCTYPE html>
<html lang="en">
<head>
<meta charset="utf-8">
<title>Ward Compass – Business Card</title>
<link rel="stylesheet" href="https://fonts.googleapis.com/css2?family=Lato:wght@400;700&family=Montserrat:wght@700&display=swap">
<style>
  :root {
    --backdrop: #b5b5b5;
    --navy: #1d396b;
    --paper: #ffffff;
    --ink: #222222;
  }
  * { margin: 0; padding: 0; box-sizing: border-box; }
  html, body { width: 1154px; height: 1200px; overflow: hidden; }
  body { background: var(--backdrop); position: relative; font-family: "Lato", Arial, sans-serif; }

  .card { position: absolute; left: 163px; width: 806px; height: 459px; overflow: hidden; }

  /* Front */
  .card-front { top: 94px; background: var(--navy); }
  .front-brand {
    position: absolute; left: 0; right: 0; top: 196px;
    display: flex; align-items: center; justify-content: center; gap: 22px;
  }
  .front-brand .brand-dot { width: 58px; height: 58px; border-radius: 50%; background: var(--paper); }
  .front-brand .brand-name {
    font-family: "Montserrat", Arial, sans-serif; font-weight: 700;
    font-size: 44px; letter-spacing: 0.5px; color: var(--paper); text-transform: uppercase;
  }

  /* Back */
  .card-back { top: 590px; background: var(--paper); }
  .back-brand {
    position: absolute; right: 32px; top: 50px;
    display: flex; align-items: center; gap: 14px;
  }
  .back-brand .brand-dot { width: 42px; height: 42px; border-radius: 50%; background: var(--navy); }
  .back-brand .brand-name {
    font-family: "Montserrat", Arial, sans-serif; font-weight: 700;
    font-size: 30px; color: var(--navy); text-transform: uppercase;
  }

  .person { position: absolute; left: 37px; top: 240px; }
  .person-name { font-weight: 700; font-size: 31px; color: var(--navy); line-height: 1.1; }
  .person-role { font-size: 21px; color: var(--ink); margin-top: 2px; }

  .divider { position: absolute; left: 38px; right: 30px; top: 317px; height: 2px; background: var(--navy); }

  .contact-list { position: absolute; left: 38px; top: 337px; list-style: none; }
  .contact-list li {
    display: flex; align-items: center; gap: 9px;
    font-size: 21px; color: var(--ink); height: 29px;
  }
  .contact-list svg { width: 19px; height: 19px; fill: var(--navy); flex: none; }

  .address {
    position: absolute; right: 29px; top: 366px; text-align: right;
    font-size: 21px; color: var(--ink); line-height: 29px; font-style: normal;
  }

  .footer-band { position: absolute; left: 0; right: 0; bottom: 0; height: 12px; background: var(--navy); }
</style>
</head>
<body>

  <section class="card card-front">
    <div class="front-brand">
      <span class="brand-dot"></span>
      <span class="brand-name">Ward Compass</span>
    </div>
  </section>

  <section class="card card-back">
    <div class="back-brand">
      <span class="brand-dot"></span>
      <span class="brand-name">Ward Compass</span>
    </div>

    <div class="person">
      <h1 class="person-name">Salwa Kettani</h1>
      <p class="person-role">CEO</p>
    </div>

    <div class="divider"></div>

    <ul class="contact-list">
      <li>
        <svg viewBox="0 0 24 24" aria-hidden="true"><path d="M6.6 10.8a15.1 15.1 0 0 0 6.6 6.6l2.2-2.2c.3-.3.7-.4 1-.2 1.1.4 2.3.6 3.6.6.6 0 1 .4 1 1V20c0 .6-.4 1-1 1A17 17 0 0 1 3 4c0-.6.4-1 1-1h3.5c.6 0 1 .4 1 1 0 1.3.2 2.5.6 3.6.1.3 0 .7-.2 1z"/></svg>
        +90 612 348 2175
      </li>
      <li>
        <svg viewBox="0 0 24 24" aria-hidden="true"><path d="M2 5h20v2l-10 6L2 7z M2 9l10 6 10-6v10H2z"/></svg>
        info@wardcompass.example
      </li>
      <li>
        <svg viewBox="0 0 24 24" aria-hidden="true"><circle cx="12" cy="12" r="10"/><path d="M7 6c2 1 3 3 2 5s-3 2-4 4M15 4c-1 2 0 4 2 4s3 2 2 5M13 20c0-2 1-3 3-4" stroke="#fff" stroke-width="1.4" fill="none"/></svg>
        www.wardcompass.example
      </li>
    </ul>

    <address class="address">
      14 Annakhil 7<br>
      H.R.B. Rabat, Morocco
    </address>

    <div class="footer-band"></div>
  </section>

</body>
</html>
```